Personal letterhead and stationary

I am looking for someone to design letterhead and stationary set for my personal use. I want something simple and timeless with a little bit of color. I like photography, computers and writing.

```html
<!DOCTYPE html>
<html lang="en">
<head>
<meta charset="utf-8">
<title>William James Holt — Letterhead</title>
<link rel="stylesheet" href="https://fonts.googleapis.com/css2?family=Josefin+Sans:wght@400;600;700&display=swap">
<style>
  :root {
    --paper: #ffffff;
    --sheet: #fdfdfb;
    --sheet-edge: #cfcfcf;
    --ink: #111111;
    --accent: #8aab5e;
  }
  html, body {
    margin: 0;
    padding: 0;
    width: 1200px;
    height: 1000px;
    overflow: hidden;
    background: var(--paper);
  }
  .stationery {
    display: block;
    width: 1200px;
    height: 1000px;
  }
  .rule { stroke: var(--accent); stroke-linecap: round; }
  .mark-name {
    fill: var(--accent);
    font-family: "Josefin Sans", sans-serif;
    font-weight: 700;
  }
  .name {
    fill: var(--ink);
    font-family: "Josefin Sans", sans-serif;
    font-weight: 700;
  }
  .address {
    fill: var(--ink);
    font-family: "Josefin Sans", sans-serif;
    font-weight: 600;
  }
  .sheet { fill: var(--sheet); stroke: var(--sheet-edge); stroke-width: 1.5; }
</style>
</head>
<body>
<svg class="stationery" viewBox="0 0 1200 1000" xmlns="http://www.w3.org/2000/svg">

  <!-- Letterhead lockup -->
  <g class="lockup">
    <line class="rule" x1="142" y1="122" x2="518" y2="122" stroke-width="3"/>
    <line class="rule" x1="682" y1="122" x2="1053" y2="122" stroke-width="3"/>
    <text class="mark-name" x="600" y="127" font-size="13" text-anchor="middle" textLength="150" lengthAdjust="spacing">WILLIAM JAMES HOLT</text>

    <text class="name" x="143" y="224" font-size="56" textLength="914" lengthAdjust="spacing">WILLIAM JAMES HOLT</text>

    <line class="rule" x1="142" y1="284" x2="215" y2="284" stroke-width="3"/>
    <line class="rule" x1="978" y1="284" x2="1053" y2="284" stroke-width="3"/>
    <text class="address" x="230" y="290" font-size="17" textLength="735" lengthAdjust="spacing">2750 APERTURE AVENUE, SAN FRANCISCO, CA 94117</text>
  </g>

  <!-- Letterhead sheet -->
  <g class="letter-sheet">
    <rect class="sheet" x="607.5" y="493.5" width="468" height="520"/>
    <line class="rule" x1="625" y1="522" x2="805" y2="522" stroke-width="2.5"/>
    <line class="rule" x1="882" y1="522" x2="1059" y2="522" stroke-width="2.5"/>
    <text class="mark-name" x="843" y="525" font-size="6.5" text-anchor="middle" textLength="68" lengthAdjust="spacing">WILLIAM JAMES HOLT</text>

    <text class="name" x="625" y="572" font-size="29" textLength="435" lengthAdjust="spacing">WILLIAM JAMES HOLT</text>

    <line class="rule" x1="625" y1="599" x2="660" y2="599" stroke-width="2.5"/>
    <line class="rule" x1="1023" y1="599" x2="1059" y2="599" stroke-width="2.5"/>
    <text class="address" x="667" y="602" font-size="8.5" textLength="350" lengthAdjust="spacing">2750 APERTURE AVENUE, SAN FRANCISCO, CA 94117</text>
  </g>
</svg>
</body>
</html>
```